The Brandwell Firm

We need a new design for our letterhead and envelopes. We are a personal injury and criminal defense firm so we need something modern and clean, but more on the professional/traditional side. Our new logo has two colors and is attached to the file so we need something that works well with those colors/matches the design. The following information needs to be on the letterhead:
Phone: (555) 214-3370
Fax: (555) 214-5186
Toll-Free: (888) 431-2059
Post Office Box 4721
Millbrook, SC 29555-4721
HarmClaimCounsel.example
PalmettoTrialAdvocates.example

Target Market(s)

Clients, government agencies, other law firms

Industry/Entity Type

Legal

Font styles to use
Sans Serif
Other font styles liked:
• Arial

Colors

Designer to choose colors to be used in the design.

Requirements
Must have
• Must look professional and clean, modern
Nice to have
• I would like to see a design that works with the logo but does not distract from the content that will be printed on it
Should not have
• Too many colors or crazy designs.

```html
<!DOCTYPE html>
<html lang="en">
<head>
<meta charset="utf-8">
<title>The Brandwell Firm — Letterhead</title>
<link href="https://fonts.googleapis.com/css2?family=Open+Sans:wght@400;600&display=swap" rel="stylesheet">
<style>
  :root {
    --firm-red: #d71f26;
    --firm-blue: #2e3191;
    --ink: #3a3a3a;
    --rule: #7a7dbf;
    --backdrop: #e6e6e6;
    --paper: #ffffff;
  }
  * { margin: 0; padding: 0; box-sizing: border-box; }
  html, body {
    width: 1200px; height: 1200px; overflow: hidden;
    background: var(--backdrop);
    font-family: "Open Sans", Arial, sans-serif;
  }
  .letterhead {
    position: absolute; left: 171px; top: 30px;
    width: 857px; height: 1140px;
    background: var(--paper);
  }
  .brand {
    position: absolute; left: 54px; top: 118px;
    display: flex; align-items: center; gap: 10px;
  }
  .brand-dot {
    width: 18px; height: 18px; border-radius: 50%;
    background: var(--firm-blue);
  }
  .brand-name {
    font-size: 27px; font-weight: 600; color: var(--firm-red);
    line-height: 1; letter-spacing: 0.2px;
  }
  .header-rule {
    position: absolute; left: 54px; right: 53px; top: 162px;
    height: 1px; background: var(--rule);
  }
  .contact {
    position: absolute; right: 53px; top: 96px;
    font-size: 12.5px; color: var(--ink); line-height: 19px;
  }
  .contact-line { display: flex; align-items: center; white-space: nowrap; }
  .contact-item { display: inline-flex; align-items: center; margin-right: 9px; }
  .contact-item:last-child { margin-right: 0; }
  .contact-item svg { width: 11px; height: 11px; margin-right: 6px; fill: none; stroke: var(--firm-red); }
  .contact-item svg.solid { fill: var(--firm-red); stroke: none; }
  .footer-band {
    position: absolute; left: 0; right: 0; bottom: 0; height: 9px;
    display: flex;
  }
  .footer-band .red { flex: 1; background: var(--firm-red); }
  .footer-band .blue { flex: 1; background: var(--firm-blue); }
</style>
</head>
<body>
  <main class="letterhead">
    <div class="brand">
      <span class="brand-dot"></span>
      <span class="brand-name">The Brandwell Firm</span>
    </div>

    <div class="contact">
      <div class="contact-line">P.O. Box 4721 Millbrook, SC 29555-4721</div>
      <div class="contact-line">
        <span class="contact-item">
          <svg class="solid" viewBox="0 0 24 24"><path d="M6.6 10.8a15 15 0 0 0 6.6 6.6l2.2-2.2a1 1 0 0 1 1-.25 11.4 11.4 0 0 0 3.6.6 1 1 0 0 1 1 1V20a1 1 0 0 1-1 1A17 17 0 0 1 3 4a1 1 0 0 1 1-1h3.5a1 1 0 0 1 1 1c0 1.25.2 2.45.6 3.6a1 1 0 0 1-.25 1z"/></svg>
          (555) 214-3370
        </span>
        <span class="contact-item">
          <svg class="solid" viewBox="0 0 24 24"><path d="M6 2h12v5H6zM3 8h18a1 1 0 0 1 1 1v8h-4v5H6v-5H2V9a1 1 0 0 1 1-1zm5 8v4h8v-4z"/></svg>
          (555) 214-5186
        </span>
        <span class="contact-item">
          <svg class="solid" viewBox="0 0 24 24"><path d="M6.6 10.8a15 15 0 0 0 6.6 6.6l2.2-2.2a1 1 0 0 1 1-.25 11.4 11.4 0 0 0 3.6.6 1 1 0 0 1 1 1V20a1 1 0 0 1-1 1A17 17 0 0 1 3 4a1 1 0 0 1 1-1h3.5a1 1 0 0 1 1 1c0 1.25.2 2.45.6 3.6a1 1 0 0 1-.25 1z"/></svg>
          (888) 431-2059
        </span>
      </div>
      <div class="contact-line">
        <span class="contact-item">
          <svg viewBox="0 0 24 24" stroke-width="2"><circle cx="12" cy="12" r="10"/><path d="M2 12h20M12 2c3 3 3 17 0 20M12 2c-3 3-3 17 0 20"/></svg>
          PalmettoTrialAdvocates.example
        </span>
        <span class="contact-item">
          <svg viewBox="0 0 24 24" stroke-width="2"><circle cx="12" cy="12" r="10"/><path d="M2 12h20M12 2c3 3 3 17 0 20M12 2c-3 3-3 17 0 20"/></svg>
          HarmClaimCounsel.example
        </span>
      </div>
    </div>

    <div class="header-rule"></div>

    <div class="footer-band"><span class="red"></span><span class="blue"></span></div>
  </main>
</body>
</html>
```